Specialised investor in e-mobility and energy wants business card design

We need a business card design that fits our existing corporate design. <The look and feel must be 'sharp'/'clean', dynamic, communicate momentum, professionalism etc (as one would imagine from a firm in the financial sector). We like the idea of a reverse-side of the card that includes the logo, and the name and contact details on the other. We expect the deliverable to be whatever format might be required to be able to get cards printed directly by a service such as kelmo press. Our website is www.zub.capital

```html
<!DOCTYPE html>
<html lang="en">
<head>
<meta charset="utf-8">
<title>Zub Capital – Business Card</title>
<link rel="stylesheet" href="https://fonts.googleapis.com/css2?family=Montserrat:wght@400;500;700&display=swap">
<style>
  :root {
    --backdrop: #2b2d31;
    --card: #17181b;
    --accent: #7dbb35;
    --ink: #ffffff;
    --muted: #d9d9d9;
    --rule: #bdbdbd;
  }
  * { box-sizing: border-box; margin: 0; padding: 0; }
  html, body { width: 1200px; height: 952px; overflow: hidden; }
  body {
    background: var(--backdrop);
    font-family: "Montserrat", sans-serif;
    display: flex;
    align-items: center;
    justify-content: center;
    gap: 40px;
  }
  .card {
    position: relative;
    width: 540px;
    height: 310px;
    background: var(--card);
    border-radius: 22px;
    border-bottom: 8px solid var(--accent);
    overflow: hidden;
    color: var(--ink);
  }
  .wordmark {
    display: flex;
    align-items: center;
    gap: 14px;
    font-weight: 500;
    color: var(--ink);
    letter-spacing: 0.5px;
  }
  .wordmark-mark {
    width: 22px; height: 22px;
    background: var(--accent);
  }
  .card-front .wordmark {
    position: absolute;
    inset: 0;
    justify-content: center;
    font-size: 46px;
  }
  .card-back .wordmark {
    position: absolute;
    top: 40px;
    left: 0; right: 0;
    justify-content: center;
    font-size: 38px;
  }
  .divider {
    position: absolute;
    top: 140px;
    left: 0; right: 0;
    height: 1px;
    background: var(--rule);
  }
  .identity {
    position: absolute;
    top: 118px;
    left: 0; right: 0;
    text-align: center;
  }
  .identity-name {
    display: inline-block;
    background: var(--card);
    padding: 0 12px;
    color: var(--accent);
    font-weight: 700;
    font-size: 24px;
    letter-spacing: 0.5px;
  }
  .identity-role {
    display: block;
    margin-top: 2px;
    font-size: 13px;
    color: var(--muted);
  }
  .contacts {
    position: absolute;
    top: 205px;
    display: flex;
    flex-direction: column;
    gap: 10px;
    font-size: 13px;
    color: var(--muted);
  }
  .contacts-left { left: 34px; }
  .contacts-right { right: 34px; align-items: flex-end; }
  .contact { display: flex; align-items: center; gap: 10px; }
  .contact-icon {
    width: 18px; height: 18px;
    border-radius: 4px;
    background: var(--accent);
    display: flex; align-items: center; justify-content: center;
  }
  .contact-icon svg { width: 12px; height: 12px; fill: var(--card); }
</style>
</head>
<body>
  <section class="card card-front" aria-label="Card front">
    <div class="wordmark"><span class="wordmark-mark"></span>Zub Capital</div>
  </section>

  <section class="card card-back" aria-label="Card back">
    <div class="wordmark"><span class="wordmark-mark"></span>Zub Capital</div>
    <div class="divider"></div>
    <div class="identity">
      <span class="identity-name">ELIN VARGA</span>
      <span class="identity-role">Manager</span>
    </div>
    <div class="contacts contacts-left">
      <div class="contact">
        <span class="contact-icon"><svg viewBox="0 0 24 24"><path d="M6.6 10.8a15 15 0 0 0 6.6 6.6l2.2-2.2a1 1 0 0 1 1-.25 11.4 11.4 0 0 0 3.6.57 1 1 0 0 1 1 1V20a1 1 0 0 1-1 1A17 17 0 0 1 3 4a1 1 0 0 1 1-1h3.5a1 1 0 0 1 1 1c0 1.25.2 2.45.57 3.57a1 1 0 0 1-.25 1z"/></svg></span>
        +41 79 555 0147
      </div>
      <div class="contact">
        <span class="contact-icon"><svg viewBox="0 0 24 24"><path d="M2 5h20v14H2zm2 2v.5l8 5 8-5V7l-8 5z"/></svg></span>
        elin@zub.capital
      </div>
    </div>
    <div class="contacts contacts-right">
      <div class="contact">
        Lausanne, Switzerland
        <span class="contact-icon"><svg viewBox="0 0 24 24"><path d="M12 2a7 7 0 0 0-7 7c0 5 7 13 7 13s7-8 7-13a7 7 0 0 0-7-7zm0 9.5A2.5 2.5 0 1 1 12 6.5a2.5 2.5 0 0 1 0 5z"/></svg></span>
      </div>
      <div class="contact">
        www.zub.capital
        <span class="contact-icon"><svg viewBox="0 0 24 24"><path d="M5 3l14 8-6 1.5 3.5 7-2.5 1.2-3.5-7L6 18z"/></svg></span>
      </div>
    </div>
  </section>
</body>
</html>
```